New Business Card Design Project

Need a design that will create an impact / strong impression towards our clients for our business. We are in the lighting business and we do lighting retrofits for large commercial to industrial clientele.

Target Market(s)

Lighting Industry

Industry/Entity Type

Business

Font styles to use
Other font styles liked:
• we would like to use the font on our logo, not sure what it is though..

Requirements
Must have
• Our logo.
Nice to have
• We are open to suggestions that have to do with lighting.

```html
<!DOCTYPE html>
<html lang="en">
<head>
<meta charset="utf-8">
<title>Brightway Retrofit Group – Business Card</title>
<link href="https://fonts.googleapis.com/css2?family=Source+Sans+3:wght@400;600;700&display=swap" rel="stylesheet">
<style>
  :root {
    --backdrop: #1b1b1b;
    --card-light: #f2f2f2;
    --green-deep: #16803a;
    --green-bright: #6cc55a;
    --green-brand: #1d6b2c;
    --green-accent: #1f8b3b;
    --green-name: #163f1a;
    --ink: #1a1a1a;
    --white: #ffffff;
  }
  * { margin: 0; padding: 0; box-sizing: border-box; }
  html, body {
    width: 1200px; height: 900px; overflow: hidden;
    background: var(--backdrop);
    font-family: "Source Sans 3", "Myriad Pro", sans-serif;
  }
  .canvas { position: relative; width: 1200px; height: 900px; }
  .card {
    position: absolute; top: 170px; width: 347px; height: 561px;
  }
  .card--front { left: 259px; background: var(--card-light); color: var(--ink); }
  .card--back {
    left: 631px;
    background: linear-gradient(135deg, var(--green-deep) 0%, var(--green-bright) 40%, var(--green-bright) 60%, var(--green-deep) 100%);
  }
  .brand {
    position: absolute; left: 0; right: 0;
    display: flex; align-items: center; justify-content: center; gap: 10px;
    font-weight: 700; font-size: 32px; letter-spacing: 1px;
  }
  .brand__mark { width: 22px; height: 22px; }
  .card--front .brand { top: 140px; color: var(--green-brand); }
  .card--front .brand__mark { background: var(--green-brand); }
  .card--back .brand { top: 258px; color: var(--white); }
  .card--back .brand__mark { background: var(--white); }
  .contact {
    position: absolute; top: 325px; left: 0; right: 0;
    text-align: center; font-size: 15px; line-height: 21px;
  }
  .contact__name { font-size: 23px; font-weight: 700; color: var(--green-name); line-height: 28px; }
  .contact__role { font-size: 15px; margin-top: 1px; }
  .contact__rule {
    width: 130px; height: 1px; background: var(--green-accent);
    margin: 12px auto 14px;
  }
  .contact__label { font-weight: 700; }
  .contact__web { font-weight: 600; }
  .contact__web span { color: var(--green-accent); }
  .contact__address { margin-top: 13px; line-height: 17px; }
</style>
</head>
<body>
<div class="canvas">
  <section class="card card--front">
    <div class="brand"><span class="brand__mark"></span>BRIGHTWAY</div>
    <div class="contact">
      <p class="contact__name">JOHN SMITH</p>
      <p class="contact__role">Managing Director</p>
      <div class="contact__rule"></div>
      <p><span class="contact__label">P:</span> 823-456-7890</p>
      <p><span class="contact__label">E:</span> info@youremail.com</p>
      <p class="contact__web">www.<span>websitename</span>.com</p>
      <p class="contact__address">1234, Address Goes Here<br>Country Name, 123456</p>
    </div>
  </section>
  <section class="card card--back">
    <div class="brand"><span class="brand__mark"></span>BRIGHTWAY</div>
  </section>
</div>
</body>
</html>
```